Verdant Systems Business Card

want the back of card to be blue- with the logo in the center
front of card- info plus logo (info being mailing address, email address, and website address )
4 different names with titles to have on cards
1) Calvin Borsted - Owner
2) Naomi Trelvik- Customer Relationship Specialist
3) Felix Andrade- Vice President of Sales
4) Owen Markby- Chief Technology Officer

Target Market(s)

tech company in the government/probation office industry

Industry/Entity Type

Government Office

Contact Information for Business Card

1) Calvin Borsted - Owner

Colors
0355a3
ffffff

Requirements
Must have
• back side should be blue, with the logo placed in the center
• front side needs to include both the logo, as well as company info (info should include website address, email address, and mailing address)

```html
<!DOCTYPE html>
<html lang="en">
<head>
<meta charset="utf-8">
<title>Verdant Systems Business Card</title>
<link rel="stylesheet" href="https://fonts.googleapis.com/css2?family=Noto+Serif:wght@500&family=Roboto:wght@400&display=swap">
<style>
  :root {
    --navy: #24386b;
    --navy-deep: #172650;
    --grey: #85858f;
    --band-grey: #8f8f9a;
    --paper: #fbfbfa;
    --white: #ffffff;
    --backdrop: #b0aeae;
  }
  * { box-sizing: border-box; margin: 0; padding: 0; }
  html, body { width: 1200px; height: 1200px; overflow: hidden; }
  body {
    background: var(--backdrop);
    position: relative;
    font-family: "Roboto", Arial, sans-serif;
  }
  .card {
    position: absolute;
    width: 712px;
    height: 417px;
    border-radius: 22px;
    overflow: hidden;
    box-shadow: 0 10px 28px rgba(0,0,0,0.18);
  }
  .card--back { left: 238px; top: 120px; background: var(--navy); }
  .card--front { left: 231px; top: 644px; background: var(--paper); }
  .band {
    position: absolute; left: 0; right: 0; bottom: 0; height: 16px;
    display: flex;
  }
  .band__navy { flex: 0 0 50%; background: var(--navy); }
  .band__grey { flex: 1; background: var(--band-grey); }
  .card--back .band__navy { background: var(--navy-deep); }
  .wordmark {
    font-family: "Noto Serif", Georgia, serif;
    font-weight: 500;
    color: var(--navy);
    text-transform: uppercase;
    text-align: center;
    line-height: 1.02;
  }
  .card--back .wordmark {
    position: absolute; left: 0; right: 0; top: 150px;
    font-size: 62px;
    letter-spacing: 1px;
    color: var(--white);
  }
  .site-line {
    position: absolute; left: 0; right: 0; top: 374px;
    display: flex; align-items: center; justify-content: center; gap: 22px;
    color: var(--white); font-size: 17px;
  }
  .site-line__dash { width: 48px; height: 3px; background: var(--white); border-radius: 2px; }
  .card--front .wordmark {
    position: absolute; left: 28px; width: 310px; top: 148px;
    font-size: 44px;
    letter-spacing: 0.5px;
  }
  .details { position: absolute; left: 368px; top: 96px; color: var(--grey); }
  .details__name {
    font-family: "Noto Serif", Georgia, serif; font-weight: 500;
    color: var(--navy); font-size: 25px; letter-spacing: 0.5px;
    text-transform: uppercase;
  }
  .details__title { font-size: 18.5px; margin-top: 4px; }
  .details__address { font-size: 18.5px; line-height: 30px; margin-top: 16px; }
  .contact { list-style: none; margin-top: 4px; font-size: 18.5px; }
  .contact li { display: flex; align-items: center; height: 26.5px; }
  .contact svg { width: 16px; height: 16px; margin-right: 14px; fill: var(--navy); flex: none; }
  .contact .icon-globe { fill: none; stroke: var(--navy); stroke-width: 1.5; }
</style>
</head>
<body>
  <section class="card card--back" aria-label="Card back">
    <div class="wordmark">Verdant<br>Systems</div>
    <div class="site-line">
      <span class="site-line__dash"></span>
      <span>www.verdantsystems.com</span>
      <span class="site-line__dash"></span>
    </div>
    <div class="band"><span class="band__navy"></span><span class="band__grey"></span></div>
  </section>

  <section class="card card--front" aria-label="Card front">
    <div class="wordmark">Verdant<br>Systems</div>
    <div class="details">
      <p class="details__name">Naomi Trelvik</p>
      <p class="details__title">Customer Relationship Specialist</p>
      <p class="details__address">234 Anywhere St., Any City,<br>Any Town, US 123456</p>
      <ul class="contact">
        <li><svg viewBox="0 0 16 16" aria-hidden="true"><path d="M1 5c0-2 3-3 7-3s7 1 7 3v1h-4V4.5H5V6H1zM3 7h10l1 7H2zm5 1.5a2.2 2.2 0 1 0 0 4.4 2.2 2.2 0 0 0 0-4.4z"/></svg>111-111-1111</li>
        <li><svg viewBox="0 0 16 16" aria-hidden="true"><path d="M1 3h14v1.2L8 9 1 4.2zm0 2.6 7 4.8 7-4.8V13H1z"/></svg>naomi.t@verdantsystems.com</li>
        <li><svg class="icon-globe" viewBox="0 0 16 16" aria-hidden="true"><circle cx="8" cy="8" r="6.5"/><ellipse cx="8" cy="8" rx="2.8" ry="6.5"/><path d="M1.5 8h13"/></svg>www.verdantsystems.com</li>
      </ul>
    </div>
    <div class="band"><span class="band__navy"></span><span class="band__grey"></span></div>
  </section>
</body>
</html>
```